KTR Design Business Card

I need to develop a business card for my real estate design and investment company. Something clean, classic and professional with a modern vibe.

Industry/Entity Type

Real Estate

Font styles to use
Serif
Sans Serif

```html
<!DOCTYPE html>
<html lang="en">
<head>
<meta charset="utf-8">
<title>KTR Design Business Card</title>
<link rel="stylesheet" href="https://fonts.googleapis.com/css2?family=Montserrat:wght@400;500;600&family=Questrial&display=swap">
<style>
  :root {
    --page-bg: #e6e7ea;
    --card-white: #fbfbfb;
    --card-fade: #e9e9e9;
    --corner-dark: #3a3a3a;
    --corner-mid: #8e8e8e;
    --corner-light: #d4d4d4;
    --ink: #333333;
    --ink-soft: #4a4a4a;
  }
  * { box-sizing: border-box; margin: 0; padding: 0; }
  html, body { width: 1200px; height: 840px; overflow: hidden; }
  body {
    background: var(--page-bg);
    display: flex; align-items: center; justify-content: center;
    font-family: "Montserrat", Arial, sans-serif;
    color: var(--ink);
  }
  .business-card {
    position: relative;
    width: 1000px; height: 572px;
    background: radial-gradient(ellipse at 60% 40%, var(--card-white) 0%, #f3f3f3 55%, var(--card-fade) 100%);
    box-shadow: 0 6px 24px rgba(0,0,0,0.12);
    overflow: hidden;
  }
  .corner-accent {
    position: absolute; top: 0; right: 0;
    width: 520px; height: 270px;
    border-bottom-left-radius: 100% 100%;
    background: linear-gradient(200deg, var(--corner-dark) 0%, var(--corner-mid) 55%, var(--corner-light) 100%);
  }
  .brand {
    position: absolute; left: 60px; top: 150px;
    display: flex; align-items: center; gap: 14px;
  }
  .brand-mark { width: 18px; height: 18px; background: var(--ink); }
  .brand-name {
    font-family: "Questrial", Arial, sans-serif;
    font-size: 44px; font-weight: 400; letter-spacing: 1px; color: var(--ink);
  }
  .address {
    position: absolute; left: 64px; top: 262px;
    font-size: 17px; font-weight: 600; line-height: 1.45; letter-spacing: 0.5px;
    color: var(--ink-soft);
  }
  .contact-list {
    position: absolute; left: 64px; top: 362px;
    list-style: none;
    font-size: 15px; letter-spacing: 0.8px; color: var(--ink-soft);
  }
  .contact-list li { display: flex; align-items: center; gap: 12px; height: 30px; }
  .contact-list svg { width: 16px; height: 16px; fill: var(--ink); flex: none; }
  .person {
    position: absolute; right: 60px; top: 262px; text-align: right;
  }
  .person-name {
    font-size: 26px; font-weight: 500; letter-spacing: 1.5px; text-transform: uppercase; color: var(--ink);
  }
  .person-title {
    font-size: 17px; font-weight: 500; letter-spacing: 0.8px; color: var(--ink-soft); margin-top: 2px;
  }
</style>
</head>
<body>
  <section class="business-card">
    <div class="corner-accent" role="img" aria-label="Decorative corner in dark and light grey tones"></div>

    <div class="brand">
      <span class="brand-mark"></span>
      <span class="brand-name">KTR Design</span>
    </div>

    <p class="address">214, 9th floor, Crest Tower<br>Harbor Lane Road</p>

    <ul class="contact-list">
      <li><svg viewBox="0 0 16 16"><path d="M3 1l3 3-1.6 2c.9 2 2.6 3.7 4.6 4.6L11 9l3 3-2 2.5C6 14 2 10 1.5 3z"/></svg>012 555 0148</li>
      <li><svg viewBox="0 0 16 16"><path d="M4.5 0h7a1 1 0 011 1v14a1 1 0 01-1 1h-7a1 1 0 01-1-1V1a1 1 0 011-1zm.5 2v10h6V2zm3 11a1 1 0 100 2 1 1 0 000-2z"/></svg>012 555 0148</li>
      <li><svg viewBox="0 0 16 16"><path d="M4 0h6v5H4zM2 6h12v10H2zm2 2v2h2V8zm4 0v2h2V8zM4 12v2h2v-2zm4 0v2h2v-2z"/></svg>012 555 0148</li>
      <li><svg viewBox="0 0 16 16"><path d="M0 3h16v10H0zm1.5 1.5v.3L8 9l6.5-4.2v-.3zM1.5 6.5v5h13v-5L8 10.7z"/></svg>hello@ktrmail.com</li>
      <li><svg viewBox="0 0 16 16"><path d="M8 0a8 8 0 100 16A8 8 0 008 0zm0 1.5c.8 0 1.8 1.6 2.2 4H5.8C6.2 3.1 7.2 1.5 8 1.5zM1.6 7h2.8a14 14 0 000 2H1.6a6.5 6.5 0 010-2zm4.2 0h4.4a12 12 0 010 2H5.8a12 12 0 010-2zm5.8 0h2.8a6.5 6.5 0 010 2h-2.8a14 14 0 000-2zM5.8 10.5h4.4c-.4 2.4-1.4 4-2.2 4s-1.8-1.6-2.2-4z"/></svg>www.ktrdesign-web.com</li>
    </ul>

    <div class="person">
      <p class="person-name">Daniel Morrow</p>
      <p class="person-title">Managing Director</p>
    </div>
  </section>
</body>
</html>
```